Maple Grove Schools | brand new stationery!

We need stationery design with our new logo! Our company updated it's name and image and we like to incorporate the new one on our stationery, business cards and email signature. We are looking for fresh, new ideas!
Industry: Childcare, Elementary and Middle School
Company Name: Maple Grove Schools
Tagline: Bright Futures Start Here
Main colors: Blue, white and a little yellow
Star shape is something new for us! Do you see a way to incorporate it as a design element?

```html
<!DOCTYPE html>
<html lang="en">
<head>
<meta charset="utf-8">
<title>Maple Grove Schools — Business Cards</title>
<link rel="stylesheet" href="https://fonts.googleapis.com/css2?family=Montserrat:wght@400;500;700&family=Poppins:wght@500;600&display=swap">
<style>
  :root {
    --navy: #0b1f7a;
    --ink: #1c1c1c;
    --charcoal: #231f20;
    --paper: #ffffff;
    --gold: #f5b90f;
    --backdrop: #d6d6d6;
    --muted: #3a3a3a;
  }
  * { box-sizing: border-box; margin: 0; padding: 0; }
  html, body { width: 1200px; height: 807px; overflow: hidden; }
  body {
    background: var(--backdrop);
    font-family: "Montserrat", Arial, sans-serif;
    position: relative;
  }
  .card {
    position: absolute;
    width: 540px;
    height: 309px;
    overflow: hidden;
    box-shadow: 0 14px 30px rgba(0,0,0,0.28);
  }

  /* Front card */
  .card-front {
    left: 50px; top: 90px;
    background: var(--paper);
    border: 3px solid var(--navy);
  }
  .brand-row {
    position: absolute; left: 34px; top: 40px;
    display: flex; align-items: center; gap: 16px;
  }
  .brand-dot {
    width: 48px; height: 48px; border-radius: 50%;
    background: var(--navy); flex: none;
  }
  .brand-name {
    font-weight: 700; font-size: 33px; color: var(--ink);
    letter-spacing: -0.3px; white-space: nowrap;
  }
  .details {
    position: absolute; left: 36px; top: 128px;
    display: flex; align-items: center; gap: 22px;
  }
  .person-name {
    color: var(--navy); font-weight: 700; font-size: 16px;
    letter-spacing: 0.4px; text-transform: uppercase;
  }
  .person-role {
    color: var(--muted); font-size: 13px; font-weight: 500; margin-top: 3px;
  }
  .divider { width: 1.5px; height: 62px; background: var(--navy); }
  .contact-list { list-style: none; display: grid; gap: 6px; }
  .contact-list li {
    display: flex; align-items: center; gap: 9px;
    font-size: 13px; color: var(--ink); font-weight: 500;
  }
  .contact-list svg { width: 13px; height: 13px; fill: var(--navy); flex: none; }
  .address-band {
    position: absolute; left: 0; right: 0; top: 220px; height: 34px;
    background: var(--navy); color: var(--paper);
    font-size: 14px; font-weight: 500;
    display: flex; align-items: center; padding-left: 36px;
    letter-spacing: 0.3px;
  }

  /* Back card */
  .card-back {
    left: 610px; top: 400px;
    background: var(--charcoal);
    display: flex; flex-direction: column; align-items: center; justify-content: center;
    text-align: center;
  }
  .back-dot {
    width: 60px; height: 60px; border-radius: 50%;
    background: var(--navy); margin-bottom: 16px;
  }
  .back-name {
    color: var(--paper); font-weight: 700; font-size: 38px; line-height: 1.1;
    letter-spacing: -0.3px;
  }
  .tagline {
    margin-top: 16px;
    font-family: "Poppins", Arial, sans-serif;
    color: var(--gold); font-weight: 500; font-size: 24px;
  }
</style>
</head>
<body>
  <section class="card card-front" aria-label="Business card front">
    <div class="brand-row">
      <span class="brand-dot"></span>
      <span class="brand-name">Maple Grove Schools</span>
    </div>
    <div class="details">
      <div class="person">
        <p class="person-name">Daniel Carter</p>
        <p class="person-role">Managing Director</p>
      </div>
      <span class="divider"></span>
      <ul class="contact-list">
        <li>
          <svg viewBox="0 0 24 24" aria-hidden="true"><path d="M6.6 10.8a15.1 15.1 0 0 0 6.6 6.6l2.2-2.2c.3-.3.7-.4 1-.2 1.1.4 2.3.6 3.6.6.6 0 1 .4 1 1V20c0 .6-.4 1-1 1A17 17 0 0 1 3 4c0-.6.4-1 1-1h3.5c.6 0 1 .4 1 1 0 1.2.2 2.4.6 3.6.1.3 0 .7-.2 1z"/></svg>
          055-210 384 716
        </li>
        <li>
          <svg viewBox="0 0 24 24" aria-hidden="true"><path d="M2 5h20v14H2z M2 5l10 8 10-8" fill="none" stroke="#0b1f7a" stroke-width="2.4"/></svg>
          hello@maplegrove.org
        </li>
        <li>
          <svg viewBox="0 0 24 24" aria-hidden="true"><circle cx="12" cy="12" r="9.5" fill="none" stroke="#0b1f7a" stroke-width="2"/><path d="M2.5 12h19M12 2.5c3 3 3 16 0 19M12 2.5c-3 3-3 16 0 19" fill="none" stroke="#0b1f7a" stroke-width="1.6"/></svg>
          www.maplegrove.org
        </li>
      </ul>
    </div>
    <div class="address-band">18 Orchard Lane, Springfield, 45810</div>
  </section>

  <section class="card card-back" aria-label="Business card back">
    <span class="back-dot"></span>
    <p class="back-name">Maple Grove<br>Schools</p>
    <p class="tagline">Bright Futures Start Here</p>
  </section>
</body>
</html>
```